Kestrel Facilities Business Card Design

We would now like to design business cards with the new Kestrel Facilities logo

Target Market(s)

Professional

Industry/Entity Type

Professional services

Contact Information for Business Card

Employee name, title, phone number, email address, corporate office address and logo.

Font styles to use
Sans Serif

Colors
0054AA
0677BA
7BADD7
CADEEF
E8F1F8

Requirements
Must have
• My logo
Should not have
• any other pictures or images besides my logo

```html
<!DOCTYPE html>
<html lang="en">
<head>
<meta charset="utf-8">
<title>Kestrel Facilities — Business Card</title>
<link href="https://fonts.googleapis.com/css2?family=Josefin+Sans:wght@400;600;700&display=swap" rel="stylesheet">
<style>
  :root {
    --brand-blue: #3575be;
    --brand-deep: #0054aa;
    --edge-grey: #8c8c8c;
    --ink: #1e1e1e;
    --paper: #ffffff;
    --backdrop: #e8f1f8;
  }
  * { box-sizing: border-box; margin: 0; padding: 0; }
  html, body {
    width: 1200px; height: 900px; overflow: hidden;
    background: var(--backdrop);
    font-family: "Josefin Sans", sans-serif;
  }
  .canvas {
    width: 1200px; height: 900px;
    display: flex; flex-direction: column; align-items: center; justify-content: center;
    gap: 40px;
  }
  .card {
    position: relative;
    width: 700px; height: 400px;
    background: var(--paper);
    border-radius: 26px;
    overflow: hidden;
    box-shadow: 0 6px 18px rgba(0,0,0,.12);
  }
  .wordmark {
    display: flex; align-items: center; gap: 16px;
    color: var(--brand-blue);
    font-weight: 700;
    text-transform: uppercase;
    line-height: 1;
  }
  .wordmark-square {
    background: var(--brand-blue);
    flex: none;
  }

  /* front */
  .card-front .logo-zone {
    position: absolute; left: 40px; top: 70px;
    width: 300px; height: 230px;
    display: flex; align-items: center; justify-content: center;
  }
  .card-front .wordmark { font-size: 40px; }
  .card-front .wordmark-text { display: flex; flex-direction: column; gap: 6px; }
  .card-front .wordmark-square { width: 34px; height: 34px; }
  .divider {
    position: absolute; left: 366px; top: 70px;
    width: 2px; height: 230px;
    background: var(--brand-blue);
  }
  .contact {
    position: absolute; left: 392px; top: 92px;
    color: var(--ink);
  }
  .contact-name {
    color: var(--brand-blue);
    font-weight: 700; font-size: 26px; letter-spacing: .5px;
    text-transform: uppercase;
  }
  .contact-title { font-size: 18px; margin-top: 6px; }
  .contact-address { font-size: 17px; margin-top: 14px; line-height: 1.3; }
  .contact-lines { list-style: none; margin-top: 14px; font-size: 17px; }
  .contact-lines li { display: flex; align-items: center; gap: 10px; margin-top: 6px; }
  .contact-lines li.phone { font-weight: 600; font-size: 19px; }
  .contact-lines svg { width: 16px; height: 16px; flex: none; fill: var(--brand-blue); }
  .edge-band {
    position: absolute; left: 0; bottom: 0; width: 700px; height: 22px;
  }

  /* back */
  .card-back { display: flex; align-items: center; justify-content: center; border-bottom: 6px solid var(--brand-blue); }
  .card-back .wordmark { font-size: 44px; }
  .card-back .wordmark-square { width: 40px; height: 40px; }
</style>
</head>
<body>
<main class="canvas">
  <section class="card card-front" aria-label="Business card front">
    <div class="logo-zone">
      <div class="wordmark">
        <span class="wordmark-square"></span>
        <span class="wordmark-text"><span>Kestrel</span><span>Facilities</span></span>
      </div>
    </div>
    <div class="divider"></div>
    <div class="contact">
      <p class="contact-name">Amani Okoth</p>
      <p class="contact-title">Co-Founder</p>
      <p class="contact-address">P.O Box 4410-00100<br>Nairobi, Kenya</p>
      <ul class="contact-lines">
        <li class="phone">
          <svg viewBox="0 0 16 16" aria-hidden="true"><path d="M3 1h3l1.5 4-2 1.3a8 8 0 0 0 4.2 4.2L11 8.5l4 1.5v3a2 2 0 0 1-2 2A12 12 0 0 1 1 3a2 2 0 0 1 2-2z"/></svg>
          +254-700-555012
        </li>
        <li>
          <svg viewBox="0 0 16 16" aria-hidden="true"><path d="M1 3h14v10H1z M1.5 3.5 8 9l6.5-5.5" stroke="#fff" stroke-width="1.2"/></svg>
          info@kestrelfacilities.com
        </li>
        <li>
          <svg viewBox="0 0 16 16" aria-hidden="true"><circle cx="8" cy="8" r="7"/><path d="M1 8h14M8 1c3 3 3 11 0 14M8 1c-3 3-3 11 0 14" stroke="#fff" stroke-width="1" fill="none"/></svg>
          www.kestrelfacilities.com
        </li>
      </ul>
    </div>
    <svg class="edge-band" viewBox="0 0 700 22" preserveAspectRatio="none" aria-hidden="true">
      <polygon points="0,0 330,0 315,22 0,22" fill="var(--brand-blue)"/>
      <polygon points="330,0 700,0 700,22 315,22" fill="var(--edge-grey)"/>
    </svg>
  </section>

  <section class="card card-back" aria-label="Business card back">
    <div class="wordmark"><span class="wordmark-square"></span><span>Kestrel Facilities</span></div>
  </section>
</main>
</body>
</html>
```